Branding product image: VELMOT (Golden Papaya) in Plastic Cup (Ready to Eat)

The product is sliced Fruit in Light syrup
Flavour: VELMOT (Golden Papaya)
The temporary product name: VELMOT
I want the product design to be something 'fun', 'natural', and 'colourful'
The design concept could be anything depends on your imagination, but it must be eye catchy and attractive.
Basically, I want you to be creative in designing the logo and the overall graphic design for the label.
The measurement is 20 cm (Length) x 6,5 cm (Height)
The target customers are young and health conscious audiences (10 years - 65 years old).
Create something different. Something extraordinary.
Brief summary about the fruit:
This fruit only grows in certain part of the world. It grows in mountain area that is in tropical climate. The fruit flesh has a yellowish-golden color. It has an extraordinary taste (unlike normal papaya) and it suits very well with any dishes from cold appetizer, white/ red meat, desserts, and cocktails.
I need a packaging design for Fruit Cup productThe product is sliced Fruit in Light syrup.There will be various flavours i.e. apple, lychee, peach, papaya, etc.However, you may design the product using one sample flavour (i.e. papaya) first, as the designs of other flavours could be adjusted afterwards.The temporary product name is: RICCANAI want the product design to be something 'fun', 'natural', and 'colourful'.The design concept could be anything depends on your imagination. Basically, I want you to be creative in designing the logo and the overall graphic design for the label. - Create something different. Something extraordinary -Additional:The measurement is 20cm (Length) x 5cm (Height).The target customers are young audiences (10 years - 35 years old).The product design must stand out in the supermarket shelf.It must be eye catchy and attractive.Thank you,Jordan-PLEASE REFER TO DESIGN SAMPLE ATTACHED TO HAVE A BETTER UNDERSTANDING FOR THE PRODUCT CONCEPT- Added Wednesday, September 17, 2014
Project Deadline Extended Reason: Haven't found a good design. Added Friday, September 19, 2014
Project Deadline Extended Reason: Need more time for designers to finalize and perfect the design.Thank you,Jordan Added Monday, September 29, 2014
Project Deadline Extended Reason: I haven't found a great design yet. Added Tuesday, February 24, 2015
Reason: Getting better designs now. Still Open to new ideas while refining the latest designs from some designers.
Please do your best in submitting other great designs!

```html
<!DOCTYPE html>
<html lang="en">
<head>
<meta charset="utf-8">
<title>DOSUVEL – Sliced in Light Syrup Label</title>
<link href="https://fonts.googleapis.com/css2?family=Lobster&family=Arimo:wght@400&display=swap" rel="stylesheet">
<style>
  :root {
    --page-bg: #ffffff;
    --label-edge: #f59a1c;
    --label-mid: #fdbf38;
    --label-core: #ffc942;
    --brand-green: #7cc242;
    --ribbon-red: #d9252a;
    --ribbon-dark: #9e171b;
    --ribbon-text: #ffffff;
    --body-text: #2b2115;
    --fruit-skin: #b9b04a;
    --fruit-flesh: #f58a2a;
  }
  html, body {
    margin: 0;
    width: 1145px;
    height: 1200px;
    overflow: hidden;
    background: var(--page-bg);
  }
  .canvas {
    position: relative;
    width: 1145px;
    height: 1200px;
  }
  .label {
    position: absolute;
    left: 50px;
    top: 430px;
    width: 1045px;
    height: 340px;
    background: linear-gradient(90deg, var(--label-edge) 0%, var(--label-mid) 30%, var(--label-core) 50%, var(--label-mid) 70%, var(--label-edge) 100%);
  }
  .front-panel {
    position: absolute;
    left: 50%;
    top: 0;
    width: 260px;
    height: 100%;
    transform: translateX(-50%);
  }
  .brand-name {
    position: absolute;
    left: 0;
    right: 0;
    top: 22px;
    margin: 0;
    text-align: center;
    font-family: "Lobster", cursive;
    font-weight: 400;
    font-size: 58px;
    line-height: 1;
    color: var(--brand-green);
  }
  .ribbon {
    position: absolute;
    left: 12px;
    top: 98px;
    width: 236px;
    height: 36px;
  }
  .ribbon-text {
    position: absolute;
    left: 12px;
    top: 98px;
    width: 236px;
    height: 36px;
    line-height: 36px;
    text-align: center;
    font-family: "Lobster", cursive;
    font-size: 17px;
    color: var(--ribbon-text);
    margin: 0;
  }
  .fruit-art {
    position: absolute;
    left: 32px;
    top: 150px;
    width: 196px;
    height: 118px;
  }
  .net-weight {
    position: absolute;
    left: 0;
    right: 0;
    top: 286px;
    margin: 0;
    text-align: center;
    font-family: "Arimo", Arial, sans-serif;
    font-size: 15px;
    color: var(--body-text);
    letter-spacing: 0.2px;
  }
</style>
</head>
<body>
<main class="canvas">
  <section class="label">
    <div class="front-panel">
      <h1 class="brand-name">Dosuvel</h1>

      <svg class="ribbon" viewBox="0 0 236 36" aria-hidden="true">
        <polygon points="0,8 14,4 14,34 0,30 6,19" fill="var(--ribbon-dark)"/>
        <polygon points="236,8 222,4 222,34 236,30 230,19" fill="var(--ribbon-dark)"/>
        <path d="M10,6 Q118,-2 226,6 L226,32 Q118,24 10,32 Z" fill="var(--ribbon-red)"/>
      </svg>
      <p class="ribbon-text">Sliced in Light syrup</p>

      <svg class="fruit-art" viewBox="0 0 196 118" role="img" aria-label="Illustration of a whole golden papaya beside a halved papaya with seeds">
        <defs>
          <radialGradient id="fruitTone" cx="60%" cy="50%" r="60%">
            <stop offset="0%" stop-color="var(--fruit-flesh)"/>
            <stop offset="100%" stop-color="var(--fruit-skin)"/>
          </radialGradient>
        </defs>
        <ellipse cx="98" cy="59" rx="94" ry="56" fill="url(#fruitTone)" opacity="0.85"/>
      </svg>

      <p class="net-weight">NET WT 6 OZ (170g)</p>
    </div>
  </section>
</main>
</body>
</html>
```